Dentistry

Dentist's personal business card. No logo needed. The card shoul deliver the massage of reliability, professionalism, experience.
Please ad the full brief of the project: down the line it says: the winning look should be precise and pristine NO pictures of Teeth, smiles, instruments etc.

The details to be desplaid are:
Dr. Rob Tavolen
Doctor of Dental Surgery
PHD
Web. Www.drtavolen.com
Email. Rob@drtavolen.com
Tel 07742318590
Surgery address. 27Bferndale road London SW4 8QT UK
62 Wexley Row London SW3 2HN. Uk

Reason: Decided to make the payment unrefundable in order to get more designers involved.

Requirements
Should not have
• Logo, teeth, smile any sort of instruments.

```html
<!DOCTYPE html>
<html lang="en">
<head>
<meta charset="utf-8">
<title>Dr. Rob Tavolen — Contact Card</title>
<link rel="stylesheet" href="https://fonts.googleapis.com/css2?family=Exo+2:wght@300&display=swap">
<style>
  :root {
    --card-navy: #16123b;
    --accent-blue: #0080c8;
    --text-white: #ffffff;
  }
  * { margin: 0; padding: 0; box-sizing: border-box; }
  html, body {
    width: 1200px;
    height: 777px;
    overflow: hidden;
    background: var(--card-navy);
  }
  .card {
    position: relative;
    width: 1200px;
    height: 777px;
    background: var(--card-navy);
    font-family: "Exo 2", sans-serif;
    font-weight: 300;
    color: var(--text-white);
  }
  .icon-rail {
    position: absolute;
    left: 149px;
    top: 161px;
    width: 70px;
    height: 452px;
    background: var(--accent-blue);
    border-radius: 13px;
  }
  .icon {
    position: absolute;
    left: 165px;
    width: 40px;
    height: 40px;
  }
  .icon-phone { top: 178px; }
  .icon-mail  { top: 241px; }
  .icon-web   { top: 306px; }
  .icon-pin   { top: 440px; }
  .detail {
    position: absolute;
    left: 266px;
    font-size: 45px;
    line-height: 50px;
    letter-spacing: 0.5px;
    white-space: nowrap;
  }
  .detail-phone    { top: 170px; }
  .detail-email    { top: 236px; }
  .detail-web      { top: 300px; }
  .detail-surgery  { top: 437px; }
  .detail-second   { top: 556px; }
  .divider {
    position: absolute;
    left: 266px;
    width: 784px;
    height: 4px;
    background: var(--accent-blue);
  }
  .divider-top    { top: 402px; }
  .divider-bottom { top: 521px; }
</style>
</head>
<body>
<main class="card">
  <div class="icon-rail"></div>

  <svg class="icon icon-phone" viewBox="0 0 40 40" aria-hidden="true">
    <circle cx="20" cy="20" r="17" fill="none" stroke="#fff" stroke-width="3"/>
    <path d="M15 10 q-3 10 4 20 l4 -2 -3 -5 -2 1 q-2 -5 -1 -9 l2 0 0 -6 z" fill="#fff"/>
  </svg>

  <svg class="icon icon-mail" viewBox="0 0 40 40" aria-hidden="true">
    <rect x="4" y="10" width="32" height="21" fill="none" stroke="#fff" stroke-width="2"/>
    <path d="M4 10 L20 23 L36 10 M4 31 L16 20 M36 31 L24 20" fill="none" stroke="#fff" stroke-width="2"/>
  </svg>

  <svg class="icon icon-web" viewBox="0 0 40 40" aria-hidden="true">
    <circle cx="20" cy="20" r="16" fill="#fff"/>
    <path d="M10 12 q5 -2 8 1 q1 4 -3 5 q-2 3 1 6 q0 4 -3 6 q-4 -3 -5 -9 z M24 8 q4 3 2 6 q-3 1 -1 4 q4 0 6 3 q0 5 -4 9 q-2 -4 -1 -7 q-4 -2 -3 -6 q-2 -3 1 -9 z" fill="var(--accent-blue)"/>
  </svg>

  <svg class="icon icon-pin" viewBox="0 0 40 40" aria-hidden="true">
    <path d="M20 37 C12 27 8 21 8 15 A12 12 0 0 1 32 15 C32 21 28 27 20 37 Z" fill="none" stroke="#fff" stroke-width="2.5"/>
    <circle cx="20" cy="15" r="5" fill="none" stroke="#fff" stroke-width="2.5"/>
  </svg>

  <p class="detail detail-phone">07742318590</p>
  <p class="detail detail-email">rob@drtavolen.com</p>
  <p class="detail detail-web">www.drtavolen.com</p>

  <div class="divider divider-top"></div>
  <p class="detail detail-surgery">27B Ferndale Road London SW4 8QT UK</p>
  <div class="divider divider-bottom"></div>
  <p class="detail detail-second">62 Wexley Row London SW3 2HN. Uk</p>
</main>
</body>
</html>
```